VELQUINT

1. My company will allow people to buy either stock made or custom scented aromatherapy candles, lotions,soaps,body sprays, and wax melts. As there isn't a company that allows for custom oil scent mixes but me. We are just starting with the candles and the other items will be coming later.

2. My target audience is anyone who would want to buy my product. It isn't really limited due to the nature of the product I will be providing.

3. velquint.com is the domain name (purchased from plorvex.com).

4. So what I really need is the shopping cart function. A fully coded shopping cart that will calculate shipping and sales tax if need be. I need the cart function to be just like every other major retailers shopping cart function. So they can click on an item they want and have it go into a shopping cart for the customer to then be able to go and pay for their goods. I also need help creating single pages for each product. So that each thing we make has a separate page with a description and an add to cart button.

5. I would like the color scheme to follow the logo I made. I would also like the logo top center of first page. I would like the quote " elevate your choices in aromatherapy products"

^. I basically need a checkout just like every other good website. A clear shipping area for them to populate, sales tax calculator, ya know everything a normal checkout has like tressly or dunvexa.com. I also have a vonk account already as well.

```html
<!DOCTYPE html>
<html lang="en">
<head>
<meta charset="utf-8">
<title>VELQUINT — Aromatherapy Candles</title>
<link href="https://fonts.googleapis.com/css2?family=Plus+Jakarta+Sans:wght@400;500;600;700;800&display=swap" rel="stylesheet">
<style>
:root{
  --cream:#f6eeea;
  --ink:#141414;
  --indigo:#2b1aa8;
  --royal:#2f3fe0;
  --sky:#2f8bff;
  --muted:#6b6b6b;
  --gold:#f0b323;
  --night:#0b0b0d;
  --white:#ffffff;
}
*{box-sizing:border-box;margin:0;padding:0}
html,body{width:1200px;height:4428px;overflow:hidden}
body{position:relative;background:var(--cream);font-family:"Plus Jakarta Sans",sans-serif;color:var(--ink)}
.abs{position:absolute}
.btn{position:absolute;display:flex;align-items:center;justify-content:center;border-radius:30px;background:linear-gradient(180deg,var(--royal),var(--indigo));color:#fff;font-weight:600;font-size:14px;box-shadow:0 6px 14px rgba(43,26,168,.3)}
.photo{position:absolute;overflow:hidden}
h2.section-title{position:absolute;font-size:32px;font-weight:800;letter-spacing:-.3px;text-transform:uppercase}
h2.section-title span{color:var(--indigo)}
.view-all{position:absolute;font-size:14px;color:var(--royal);text-decoration:underline;font-weight:500}

/* hero */
.hero-photo{left:0;top:0;width:1200px;height:705px;background:radial-gradient(ellipse at 50% 30%,#8a6a4a 0%,#4a3424 45%,#24180f 100%)}
.nav{left:124px;top:72px;width:954px;height:96px;border-radius:48px;background:linear-gradient(90deg,#3a2fe8,#2a18a8);display:flex;align-items:center;color:#fff;font-size:17px;font-weight:500}
.nav a{position:absolute;color:#fff;text-decoration:none}
.nav .active{color:#6fb6ff}
.brand{left:518px;top:38px;width:164px;height:164px;border-radius:50%;background:#120c3a;border:4px solid #2a18a8;display:flex;align-items:center;justify-content:center;color:#fff;font-weight:700;font-size:20px;letter-spacing:2px}
.login{left:676px;top:29px;width:124px;height:40px;border-radius:20px;background:#2f8bff;font-size:15px;display:flex;align-items:center;justify-content:center;gap:8px}
.icon-btn{position:absolute;width:42px;height:42px;border-radius:50%;background:#fff;display:flex;align-items:center;justify-content:center;top:27px}
.badge{position:absolute;top:-4px;right:-4px;width:16px;height:16px;border-radius:50%;background:#2f8bff;color:#fff;font-size:9px;display:flex;align-items:center;justify-content:center}
.hero-kicker{left:0;width:1200px;top:313px;text-align:center;color:#fff;font-size:22px;font-weight:500}
.hero-title{left:0;width:1200px;top:354px;text-align:center;color:#fff;font-size:52px;font-weight:800;letter-spacing:-1px}
.hero-sub{left:0;width:1200px;top:426px;text-align:center;color:#fff;font-size:38px;font-weight:600}
.hero-arrow{position:absolute;top:354px;width:32px;height:32px;border-radius:50%;background:#fff;display:flex;align-items:center;justify-content:center}

/* products */
.product{position:absolute;top:834px;width:232px;height:430px;text-align:center}
.product.active{background:#fff;border-radius:18px;box-shadow:0 10px 30px rgba(0,0,0,.08)}
.product .photo{left:0;top:0;width:232px;height:266px;border-radius:18px}
.product.active .photo{left:12px;top:12px;width:208px;height:238px;border-radius:12px}
.product h3{position:absolute;top:290px;width:100%;font-size:14px;font-weight:700}
.product p{position:absolute;top:316px;left:20px;right:20px;font-size:12.5px;color:var(--muted);line-height:1.55}
.product .price{position:absolute;top:370px;width:100%;font-size:17px;font-weight:700;color:var(--indigo)}
.product .btn{left:32px;top:407px;width:168px;height:40px}

/* who we are */
.who-band{left:0;top:1386px}
.who-photo{left:112px;top:1452px;width:488px;height:417px;border-radius:18px;background:linear-gradient(135deg,#6b5038,#b08c62 55%,#3c2b1f)}
.who-title{left:674px;top:1456px}
.who-text{position:absolute;left:674px;width:410px;font-size:14.5px;line-height:2.1;color:#555}
.feature{position:absolute;top:1740px;display:flex;align-items:center;gap:14px;color:var(--royal);font-size:14.5px;font-weight:600;line-height:1.5}
.feature i{width:42px;height:42px;border-radius:50%;background:linear-gradient(180deg,var(--sky),var(--indigo));display:flex;align-items:center;justify-content:center}

/* categories */
.cat{position:absolute;border-radius:18px;overflow:hidden}
.cat .label{position:absolute;left:34px;bottom:22px;color:#fff;font-weight:700;font-size:17px;text-transform:uppercase}
.cat .arrow{position:absolute;right:30px;bottom:26px}
.cat.active{border:3px solid var(--royal)}

/* testimonials */
.testi-band{left:0;top:2886px;width:1200px;height:586px;background:linear-gradient(180deg,#2a17a8 0%,#2a3fd0 55%,#2d6fc4 100%)}
.testi{position:absolute;top:3072px;height:326px;background:#fff;border-radius:16px;text-align:center}
.testi.active{border:3px solid #2f8bff}
.avatar{position:absolute;left:50%;top:-44px;margin-left:-43px;width:86px;height:86px;border-radius:50%;background:linear-gradient(180deg,#d7c3b0,#8c7362);border:3px solid #fff}
.testi.active .avatar{border-color:#2f8bff}
.testi .name{position:absolute;left:0;top:60px;width:100%;color:var(--royal);font-size:15px;font-weight:500;text-transform:uppercase}
.testi .quote{position:absolute;top:86px;left:34px;right:34px;font-size:15px;line-height:1.6;color:#333}
.testi .stars{position:absolute;left:0;top:140px;width:100%;color:var(--gold);font-size:11px;letter-spacing:1px}
.testi .body{position:absolute;top:170px;left:24px;right:24px;font-size:12.5px;line-height:2;color:#666}
.round-arrow{position:absolute;top:3218px;width:34px;height:34px;border-radius:50%;background:var(--indigo);color:#fff;display:flex;align-items:center;justify-content:center;font-size:14px}

/* updates */
.post{position:absolute;top:3613px;width:314px;height:372px}
.post .photo{left:0;top:0;width:314px;height:268px;border-radius:14px}
.post .card{position:absolute;left:26px;top:190px;width:262px;height:182px;background:#fff;border-radius:14px;text-align:center}
.post .date{position:absolute;left:80px;top:22px;width:102px;height:24px;border-radius:12px;border:1px solid #f1b35a;color:#d88f2e;font-size:11.5px;display:flex;align-items:center;justify-content:center}
.post h4{position:absolute;top:62px;left:18px;right:18px;font-size:12.5px;font-weight:500;line-height:1.9;text-transform:uppercase}
.post .more{position:absolute;left:0;top:142px;width:100%;color:var(--royal);font-size:12px;text-decoration:underline}

/* footer */
.footer{left:0;top:4067px;width:1200px;height:361px;background:var(--night);color:#fff}
.foot-brand{position:absolute;left:113px;top:57px;width:170px;height:170px;border-radius:50%;background:#16104a;display:flex;align-items:center;justify-content:center;font-weight:700;font-size:20px;letter-spacing:2px}
.foot-col{position:absolute;top:72px}
.foot-col h5{font-size:15px;font-weight:600;margin-bottom:14px}
.foot-col li{list-style:none;font-size:13.5px;height:31px;display:flex;align-items:center;gap:14px}
.foot-col li::before{content:"";width:12px;height:12px;border-radius:50%;background:#fff}
.newsletter{position:absolute;left:782px;top:72px;width:310px}
.newsletter p{font-size:13px;line-height:2.2;margin-top:14px}
.email{position:absolute;left:0;top:128px;width:306px;height:42px;border-radius:21px;background:#fff;color:#777;font-size:11.5px;display:flex;align-items:center;padding-left:48px}
.email .go{position:absolute;right:2px;top:2px;width:38px;height:38px;border-radius:50%;background:var(--royal);display:flex;align-items:center;justify-content:center}
.foot-line{position:absolute;left:112px;top:296px;width:976px;height:1px;background:#2a2a2a}
.copyright{position:absolute;left:127px;top:316px;font-size:11px}
.pay{position:absolute;top:313px;width:48px;height:26px;border-radius:4px;background:#fff}
</style>
</head>
<body>

<!-- HERO -->
<div class="photo hero-photo" role="img" aria-label="Hands pouring a pillar candle among lit aromatherapy candles"></div>
<svg class="abs" style="left:0;top:0" width="1200" height="720" viewBox="0 0 1200 720">
  <defs><linearGradient id="crescent" x1="0" x2="1"><stop offset="0" stop-color="#2a18a8"/><stop offset=".5" stop-color="#2f3fe0"/><stop offset="1" stop-color="#3a6bff"/></linearGradient></defs>
  <path d="M0 533 Q600 790 1200 533 L1200 720 L0 720 Z" fill="#f6eeea"/>
  <path d="M95 578 Q600 810 1105 578 Q600 735 95 578 Z" fill="url(#crescent)"/>
</svg>

<nav class="abs nav">
  <a class="active" style="left:46px">Home</a>
  <a style="left:144px">About Us</a>
  <a style="left:272px">Products</a>
  <a style="left:604px">Shop</a>
  <div class="abs login"><svg width="13" height="14" viewBox="0 0 13 14"><circle cx="6.5" cy="4" r="3.5" fill="#fff"/><path d="M0 14a6.5 6 0 0 1 13 0z" fill="#fff"/></svg>Login</div>
  <div class="icon-btn" style="left:816px"><svg width="18" height="16" viewBox="0 0 18 16"><path d="M9 16 1.5 8.5A4.3 4.3 0 0 1 9 2.6a4.3 4.3 0 0 1 7.5 5.9z" fill="#2f3fe0"/></svg></div>
  <div class="icon-btn" style="left:868px"><svg width="18" height="16" viewBox="0 0 18 16"><path d="M0 1h3l2 9h10l2-7H5" stroke="#2f3fe0" stroke-width="2" fill="none"/><circle cx="6" cy="14" r="1.6" fill="#2f3fe0"/><circle cx="14" cy="14" r="1.6" fill="#2f3fe0"/></svg><span class="badge">0</span></div>
</nav>
<div class="abs brand">VELQUINT</div>

<p class="abs hero-kicker">Elevate Your Choices In Aromatherapy Products</p>
<h1 class="abs hero-title">CRAFT YOUR PERFECT AROMA,</h1>
<p class="abs hero-sub">ILLUMINATE YOUR SOUL</p>
<div class="btn" style="left:383px;top:496px;width:432px;height:46px;font-size:16px;border:2px solid #fff">Explore Our Scented Aromatherapy Candles</div>
<div class="hero-arrow" style="left:97px"><svg width="8" height="12"><path d="M6 1 1 6l5 5" stroke="#333" stroke-width="1.6" fill="none"/></svg></div>
<div class="hero-arrow" style="left:1069px"><svg width="8" height="12"><path d="m2 1 5 5-5 5" stroke="#333" stroke-width="1.6" fill="none"/></svg></div>

<!-- FEATURED PRODUCTS -->
<h2 class="section-title" style="left:110px;top:764px">Featured <span>Products</span></h2>
<span class="view-all" style="left:1030px;top:775px">View All</span>

<div class="product" style="left:110px">
  <div class="photo" role="img" aria-label="Lit lavender candles among lavender flowers" style="background:linear-gradient(160deg,#8a6fd0,#4a2f8a 60%,#2b1a4a)"></div>
  <h3>LAVENDER DREAMSCAPE</h3><p>Personalize Your Peace, One Candle at a Time</p><div class="price">$ 45.00</div><div class="btn">Shop Now</div>
</div>
<div class="product active" style="left:358px">
  <div class="photo" role="img" aria-label="Rows of lit candles in dark tins" style="background:radial-gradient(circle at 50% 40%,#b07a3a,#3a2616 75%)"></div>
  <h3>OCEAN BREEZE BLISS</h3><p>Custom Scents, Tailored Tranquility</p><div class="price">$ 45.00</div><div class="btn">Shop Now</div>
</div>
<div class="product" style="left:609px">
  <div class="photo" role="img" aria-label="Ribbed cream vanilla pillar candle, lit" style="background:linear-gradient(160deg,#c9925a,#f0dcc2 50%,#8a5a32)"></div>
  <h3>VANILLA REVERIE</h3><p>Curate Your Calm with Custom Aromas.</p><div class="price">$ 45.00</div><div class="btn">Shop Now</div>
</div>
<div class="product" style="left:858px">
  <div class="photo" role="img" aria-label="Candle decorated with dried rose petals" style="background:linear-gradient(160deg,#e9e4e8,#c9b4cf 55%,#a38aa8)"></div>
  <h3>ROSE PETAL RADIANCE</h3><p>Breathe In Balance, Burn Your Bliss</p><div class="price">$ 45.00</div><div class="btn">Shop Now</div>
</div>

<!-- WHO WE ARE -->
<svg class="abs who-band" width="400" height="548" viewBox="0 0 400 548">
  <defs><linearGradient id="band" x1="0" y1="0" x2="0" y2="1"><stop offset="0" stop-color="#2f8bff"/><stop offset="1" stop-color="#2a18a8"/></linearGradient></defs>
  <path d="M0 0H215L399 548H0Z" fill="url(#band)"/>
</svg>
<div class="photo who-photo" role="img" aria-label="Hands packing candles into kraft gift boxes"></div>
<h2 class="section-title who-title">Who <span>We Are</span></h2>
<p class="who-text" style="top:1511px">Ut enim ad minima veniam, quis nostrum exercitationem ullam corporis suscipit laboriosam, nisi ut aliquid ex ea commodi consequatur?</p>
<p class="who-text" style="top:1615px">Quis autem vel eum iure reprehenderit qui in ea voluptate velit esse quam nihil molestiae consequatur, vel illum qui dolorem eum fugiat quo voluptas nulla pariatur?"</p>
<div class="feature" style="left:674px"><i><svg width="16" height="18"><rect x="3" y="5" width="10" height="12" rx="2" fill="#fff"/><path d="M8 0v4" stroke="#fff" stroke-width="2"/></svg></i><span>Hand-Poured &amp;<br>Small-Batch Crafting.</span></div>
<div class="feature" style="left:920px"><i><svg width="18" height="18"><circle cx="9" cy="9" r="7" stroke="#fff" stroke-width="2" fill="none"/><path d="M5 10c2-4 6-4 8-6" stroke="#fff" stroke-width="2" fill="none"/></svg></i><span>Eco-Friendly &amp;<br>Sustainable.</span></div>
<div class="btn" style="left:674px;top:1819px;width:144px;height:36px">Explore More</div>

<!-- CATEGORIES -->
<h2 class="section-title" style="left:0;width:1200px;text-align:center;top:2007px">Shop By <span>Product Categories</span></h2>

<div class="cat" style="left:112px;top:2080px;width:311px;height:346px;background:linear-gradient(160deg,#cfd3c8,#8f9a86 60%,#4f5b4a)" role="img" aria-label="Body spray bottle with white flowers">
  <span class="label">Body Sprays</span><svg class="arrow" width="18" height="10"><path d="M0 5h16M12 1l4 4-4 4" stroke="#fff" stroke-width="2" fill="none"/></svg></div>
<div class="cat active" style="left:443px;top:2080px;width:315px;height:346px;background:linear-gradient(180deg,#d89a7a 0%,#6aa0e0 55%,#2f6fe0 100%)" role="img" aria-label="Child applying lotion at the beach">
  <span class="label">Lotions</span><svg class="arrow" width="18" height="10"><path d="M0 5h16M12 1l4 4-4 4" stroke="#fff" stroke-width="2" fill="none"/></svg></div>
<div class="cat" style="left:777px;top:2080px;width:311px;height:346px;background:linear-gradient(160deg,#4c5a3e,#b8946a 55%,#3a3222)" role="img" aria-label="Stacked handmade soap bars tied with twine">
  <span class="label">Soaps</span><svg class="arrow" width="18" height="10"><path d="M0 5h16M12 1l4 4-4 4" stroke="#fff" stroke-width="2" fill="none"/></svg></div>
<div class="cat" style="left:112px;top:2450px;width:473px;height:344px;background:radial-gradient(ellipse at 50% 40%,#d8b48c,#5a3a22 80%)" role="img" aria-label="Two glass candles with pressed flowers">
  <span class="label">Scented Aromatherapy Candles</span><svg class="arrow" width="18" height="10"><path d="M0 5h16M12 1l4 4-4 4" stroke="#fff" stroke-width="2" fill="none"/></svg></div>
<div class="cat" style="left:608px;top:2450px;width:480px;height:344px;background:linear-gradient(160deg,#5a4a3e,#2a1e16 60%,#6a5040)" role="img" aria-label="Hands pouring wax melts into moulds">
  <span class="label">Wax Melts</span><svg class="arrow" width="18" height="10"><path d="M0 5h16M12 1l4 4-4 4" stroke="#fff" stroke-width="2" fill="none"/></svg></div>

<!-- TESTIMONIALS -->
<div class="abs testi-band"></div>
<h2 class="section-title" style="left:0;width:1200px;text-align:center;top:2952px;color:#fff">Our Happy Customers</h2>
<div class="round-arrow" style="left:52px">«</div>
<div class="round-arrow" style="left:1110px">»</div>
<div class="testi" style="left:112px;width:304px">
  <div class="avatar" role="img" aria-label="Customer portrait"></div>
  <div class="name">Maren T</div><div class="quote">Consequuntur magni dolores eos qui ratione volupta</div><div class="stars">★★★★★</div>
  <p class="body">Ut enim ad minima veniam, quis nostrum exercitationem ullam corporis suscipit laboriosam, nisi ut aliquid ex ea commodi consequatur? Quis autem vel eum iure reprehenderit qui in ea</p></div>
<div class="testi active" style="left:445px;width:308px">
  <div class="avatar" role="img" aria-label="Customer portrait"></div>
  <div class="name">Ilsa K</div><div class="quote">Consequuntur magni dolores eos qui ratione volupta</div><div class="stars">★★★★★</div>
  <p class="body">Ut enim ad minima veniam, quis nostrum exercitationem ullam corporis suscipit laboriosam, nisi ut aliquid ex ea commodi consequatur? Quis autem vel eum iure reprehenderit qui in ea</p></div>
<div class="testi" style="left:780px;width:306px">
  <div class="avatar" role="img" aria-label="Customer portrait"></div>
  <div class="name">Corvina Dale</div><div class="quote">Consequuntur magni dolores eos qui ratione volupta</div><div class="stars">★★★★★</div>
  <p class="body">Ut enim ad minima veniam, quis nostrum exercitationem ullam corporis suscipit laboriosam, nisi ut aliquid ex ea commodi consequatur? Quis autem vel eum iure reprehenderit qui in ea</p></div>

<!-- LATEST UPDATES -->
<h2 class="section-title" style="left:110px;top:3543px">Latest <span>Updates</span></h2>
<span class="view-all" style="left:1030px;top:3555px">View All</span>

<div class="post" style="left:112px">
  <div class="photo" role="img" aria-label="Hands rolling beeswax taper candles" style="background:linear-gradient(160deg,#6a4a2a,#d8a040 55%,#4a3018)"></div>
  <div class="card"><span class="date">02/01/2025</span><h4>Ut enim ad minima veniam, quis nostrum exercitationem ulla m corporis suscipit</h4><span class="more">LEARN MORE</span></div></div>
<div class="post" style="left:442px">
  <div class="photo" role="img" aria-label="Amber jar candles being filled with wax" style="background:radial-gradient(circle at 50% 40%,#e9e2d8,#5a3418 70%)"></div>
  <div class="card"><span class="date">02/01/2025</span><h4>Ut enim ad minima veniam, quis nostrum exercitationem ulla m corporis suscipit</h4><span class="more">LEARN MORE</span></div></div>
<div class="post" style="left:772px">
  <div class="photo" role="img" aria-label="Hands pouring wax into a glass candle" style="background:linear-gradient(160deg,#c84a22,#e8b08a 55%,#a43a1a)"></div>
  <div class="card"><span class="date">02/01/2025</span><h4>Ut enim ad minima veniam, quis nostrum exercitationem ulla m corporis suscipit</h4><span class="more">LEARN MORE</span></div></div>

<!-- FOOTER -->
<footer class="abs footer">
  <div class="foot-brand">VELQUINT</div>
  <div class="foot-col" style="left:373px"><h5>QUICK LINKS</h5><ul><li>Home</li><li>About Us</li><li>Shop</li><li>Reviews</li><li>Blogs</li></ul></div>
  <div class="foot-col" style="left:571px"><h5>OTHER LINKS</h5><ul><li>Contact Us</li><li>Privacy Policy</li><li>Login</li><li>Help</li></ul></div>
  <div class="newsletter"><h5 style="font-size:15px;font-weight:600">JOIN OUR NEWSLETTER</h5>
    <p>Light Up Your Inbox! Get Exclusive Offers and Aromatherapy Tips</p>
    <div class="email"><svg class="abs" style="left:20px;top:16px" width="13" height="10"><rect width="13" height="10" rx="1" fill="#555"/><path d="m0 1 6.5 5L13 1" stroke="#fff" fill="none"/></svg>Enter Email Address
      <span class="go"><svg width="12" height="10"><path d="M0 5h10M6 1l4 4-4 4" stroke="#fff" stroke-width="2" fill="none"/></svg></span></div>
  </div>
  <div class="foot-line"></div>
  <p class="copyright">(C) Copyright 2025 | All Rights Reserved</p>
  <div class="pay" style="left:760px"></div>
  <div class="pay" style="left:826px"></div>
  <div class="pay" style="left:892px"></div>
  <div class="pay" style="left:958px"></div>
  <div class="pay" style="left:1024px"></div>
</footer>

</body>
</html>
```